Bookcover: Ways to Turn Into a Bold Pathfinder

I am publishing a super-low-cost innovation book for €4,99 on Quillmere Open Press to help everyone become a great innovator: young ambitious people without college education nor a big budget. Do you want to help me?

Brief:
Design a book cover 1600 x 2560 pixels for QOP.
Main title: Ways to Turn Into a Bold Pathfinder
Sub title: mindset - insights - skills & tools
Author: Joost ter Brakel
Design: captive, and appealing to everyone
Target Group: young ambitious people without college education

For quillmere please format the height/width ratio of 1.6:1

```html
<!DOCTYPE html>
<html lang="en">
<head>
<meta charset="utf-8">
<title>Ways to Turn Into a Bold Pathfinder — Book Cover</title>
<link rel="stylesheet" href="https://fonts.googleapis.com/css2?family=Montserrat:wght@800&family=Roboto:ital,wght@1,400&family=Hind:wght@500&display=swap">
<style>
  :root {
    --page-bg: #ffffff;
    --cover-edge: #fde16a;
    --cover-center: #f8f6a2;
    --ink: #111111;
    --art-blue: #3f8fc9;
    --art-teal: #27a89a;
    --art-red: #e2405f;
    --art-orange: #f0a45a;
    --art-gold: #f2c230;
  }
  html, body {
    margin: 0;
    padding: 0;
    width: 1200px;
    height: 1200px;
    overflow: hidden;
    background: var(--page-bg);
  }
  .canvas {
    position: relative;
    width: 1200px;
    height: 1200px;
  }
  .book-cover {
    position: absolute;
    left: 250px;
    top: 40px;
    width: 700px;
    height: 1120px;
    background: radial-gradient(ellipse at 50% 45%, var(--cover-center) 0%, #f9f08a 45%, var(--cover-edge) 100%);
    overflow: hidden;
  }
  .author {
    position: absolute;
    top: 60px;
    left: 0;
    width: 100%;
    margin: 0;
    text-align: center;
    font-family: "Roboto", Arial, sans-serif;
    font-style: italic;
    font-weight: 400;
    font-size: 45px;
    line-height: 54px;
    color: var(--ink);
  }
  .title {
    position: absolute;
    top: 122px;
    left: 0;
    width: 100%;
    margin: 0;
    text-align: center;
    font-family: "Montserrat", Arial, sans-serif;
    font-weight: 800;
    font-size: 90px;
    line-height: 99px;
    letter-spacing: -1px;
    text-transform: uppercase;
    color: var(--ink);
  }
  .title span { display: block; }
  .subtitle {
    position: absolute;
    top: 522px;
    left: 0;
    width: 100%;
    margin: 0;
    text-align: center;
    font-family: "Hind", Arial, sans-serif;
    font-weight: 500;
    font-size: 40px;
    line-height: 48px;
    color: var(--ink);
  }
  .cover-art {
    position: absolute;
    left: 62px;
    top: 590px;
    width: 576px;
    height: 510px;
  }
</style>
</head>
<body>
<div class="canvas">
  <section class="book-cover">
    <p class="author">Joost ter Brakel</p>
    <h1 class="title">
      <span>Ways to</span>
      <span>Turn Into</span>
      <span>A Bold</span>
      <span>Pathfinder</span>
    </h1>
    <p class="subtitle">Mindset - Insights - Skills &amp; Tools</p>
    <svg class="cover-art" viewBox="0 0 576 510" role="img" aria-label="Dense colourful doodle cluster of innovation and business icons: light bulb, brain, gears, megaphone, charts, currency signs, speech bubbles, laptop and idea notes">
      <defs>
        <linearGradient id="art-tone" x1="0" y1="0" x2="1" y2="1">
          <stop offset="0%" stop-color="var(--art-teal)"/>
          <stop offset="30%" stop-color="var(--art-blue)"/>
          <stop offset="55%" stop-color="var(--art-red)"/>
          <stop offset="80%" stop-color="var(--art-orange)"/>
          <stop offset="100%" stop-color="var(--art-gold)"/>
        </linearGradient>
      </defs>
      <path d="M150 20 C230 -5 350 -5 430 20 C520 50 566 130 572 230 C578 340 545 430 470 480 C400 515 180 515 110 480 C30 440 0 350 4 240 C8 130 60 50 150 20 Z"
            fill="url(#art-tone)" fill-opacity="0.72"/>
    </svg>
  </section>
</div>
</body>
</html>
```